Counseling Practice Business Card

I need a professional looking business card incorporating my new logo that was just completed. Card needs to incorporate my name and title, description of my specialty, my address, my phone number, my fax number, my email and my website URL. I need to be able to choose design on/with different paper colors and textures.
I do not have a lot of business card ideas so I am open to anything but I want bold,sharp, clear card without additional designs other than my logo (see attached file info). I am open to different color backgrounds or paper colors including black. I do not like traditional brackets around area codes in phone number or dashes between numbers in phone number. Am open to other ways of presenting including periods between numbers as appropriate. I do not know enough to know what I like yet but I want card to coordinate and work together with my logo. My practice emphasizes natural mental health interventions so any use of color (with background paper color or the blue and green in my logo) that elicits nature is nice. In addition to black, any natural brown or wood looking background might be desirable also. Most of the offerings so far look very similar and boring.

Target Market(s)

Potential therapy clients and other professionals

Contact Information for Business Card

Card information:
Gerald M. Whitcombe, Ph.D.
Licensed Clinical Psychologist
Integrative Health Coach
4812 Marlowe Ridge Blvd SE
Suite 310
Duluth, GA 30096
(770) 415-2983 phone
(770) 581-4096 fax
drgeraldwhitcombe@quillmarsh.net
brightfernwellness.net

Font styles to use
Serif
Sans Serif
Other font styles liked:
• anything that you think looks crisp, clear and easily readable

Requirements
Must have
• Any color used should coordinate with my logo design (see attached files).
• Card should be printed horizontally so top and bottom are longest sides of rectangle.
• Background color or paper color should complement and highlight logo. Do not like a white background. black, grey, brown or any color my logo would blend well with.
Nice to have
• I would like designer to utilize color to highlight letters/name or phone-fax-web symbols.
• Bottom edge of card could be highlighted if appropriate to an idea.
Should not have
• I would NOT want the card to have a pure white background at all.
• No clear cards.
• Cards should be oriented with long sides on bottom and top, NOT sides. DO NOT LIKE THIS THIN TALL ORIENTATION.

```html
<!DOCTYPE html>
<html lang="en">
<head>
<meta charset="utf-8">
<title>Brightfern Wellness – Business Card</title>
<link rel="stylesheet" href="https://fonts.googleapis.com/css2?family=Roboto:wght@400;500&family=Roboto+Condensed:wght@700&display=swap">
<style>
  :root {
    --backdrop: #6e4d33;
    --card: #151619;
    --blue: #2a78be;
    --green: #1f8a3f;
    --text: #d2d3d5;
    --rule: #55575c;
    --band-text: #dfe8f2;
  }
  * { margin: 0; padding: 0; box-sizing: border-box; }
  html, body { width: 1200px; height: 960px; overflow: hidden; }
  body {
    background: var(--backdrop);
    position: relative;
    font-family: "Roboto", Arial, sans-serif;
  }
  .card {
    position: absolute;
    width: 600px;
    height: 343px;
    background: var(--card);
    box-shadow: 0 3px 8px rgba(0,0,0,0.45);
    overflow: hidden;
  }
  .card--front { left: 314px; top: 113px; }
  .card--back { left: 311px; top: 472px; }

  .brand-name {
    position: absolute;
    color: var(--blue);
    font-weight: 500;
    white-space: nowrap;
  }
  .card--front .brand-name { left: 33px; top: 58px; font-size: 30px; }
  .card--back .brand-name {
    left: 0; right: 0; top: 118px;
    text-align: center; font-size: 44px;
  }

  .holder {
    position: absolute;
    right: 32px; top: 175px;
    text-align: right;
  }
  .holder__name {
    font-family: "Roboto Condensed", "Arial Narrow", sans-serif;
    font-weight: 700;
    font-size: 19px;
    color: var(--blue);
    letter-spacing: 0.2px;
    line-height: 24px;
  }
  .holder__title {
    font-size: 15px;
    color: var(--green);
    line-height: 19px;
  }
  .accent-tab {
    position: absolute;
    right: 0; top: 173px;
    width: 12px; height: 26px;
    background: var(--blue);
  }
  .rule {
    position: absolute;
    left: 161px; top: 247px;
    width: 407px; height: 1px;
    background: var(--rule);
  }
  .contact {
    position: absolute;
    left: 33px; top: 238px;
    list-style: none;
  }
  .contact li {
    display: flex;
    align-items: center;
    height: 19.3px;
    font-size: 14px;
    color: var(--text);
  }
  .contact svg { width: 14px; height: 14px; margin-right: 9px; fill: var(--blue); }
  .address {
    position: absolute;
    right: 32px; top: 278px;
    text-align: right;
    font-size: 14px;
    line-height: 19px;
    color: var(--text);
  }

  .web-band {
    position: absolute;
    left: 0; right: 0; top: 279px;
    height: 30px;
    background: var(--blue);
    color: var(--band-text);
    font-size: 15px;
    letter-spacing: 4.2px;
    text-align: center;
    line-height: 30px;
  }
</style>
</head>
<body>

<section class="card card--front">
  <div class="brand-name">Brightfern Wellness</div>

  <div class="accent-tab"></div>
  <div class="holder">
    <div class="holder__name">GERALD M. WHITCOMBE, PH.D.</div>
    <div class="holder__title">Licensed Clinical Psychologist</div>
    <div class="holder__title">Integrative Health Coach</div>
  </div>

  <div class="rule"></div>

  <ul class="contact">
    <li>
      <svg viewBox="0 0 16 16" aria-hidden="true"><path d="M3.6 1.2l2.3 2.3c.4.4.4 1 0 1.4L4.8 6c.8 1.8 2.3 3.3 4.1 4.1l1.1-1.1c.4-.4 1-.4 1.4 0l2.3 2.3c.4.4.4 1 0 1.4l-1.3 1.3c-.6.6-1.6.8-2.4.4C6.6 13 3 9.4 1.6 6c-.4-.8-.2-1.8.4-2.4l1.3-1.3c0-.4.7-.4.3-1.1z"/></svg>
      (770) 415-2983
    </li>
    <li>
      <svg viewBox="0 0 16 16" aria-hidden="true"><path d="M4 1h8v4H4zM1 6h14v6h-2v-2H3v2H1zM4 11h8v4H4z"/></svg>
      (770) 581-4096
    </li>
    <li>
      <svg viewBox="0 0 16 16" aria-hidden="true"><path d="M1 3h14v10H1zM2 4l6 5 6-5v1L8 10 2 5z" fill-rule="evenodd"/></svg>
      drgeraldwhitcombe@quillmarsh.net
    </li>
    <li>
      <svg viewBox="0 0 16 16" aria-hidden="true"><circle cx="8" cy="8" r="7"/><path d="M1 8h14M8 1c-3 3.5-3 10.5 0 14M8 1c3 3.5 3 10.5 0 14" stroke="#151619" stroke-width="1.1" fill="none"/></svg>
      www.brightfernwellness.net
    </li>
  </ul>

  <div class="address">
    4812 Marlowe Ridge Blvd SE<br>
    Suite 310, Duluth, GA 30096
  </div>
</section>

<section class="card card--back">
  <div class="brand-name">Brightfern Wellness</div>
  <div class="web-band">www.brightfernwellness.net</div>
</section>

</body>
</html>
```